energy rating company

Web Design graphics and layout only

To create two pages for the website. First the home page and the second is the design for the job board for our clients use after login. I have attached files that explain in detail what the pages should have and the purpose/desires of each object. Please read these thoroughly.

The webpages need to be clean, professional, easy on the eye, obvious in all its buttons and functions with a strong call to action on the home page and branding and clean, great and obvious looking buttons and very simple but dynamic as well. We wish to be seen as contemporary.

Business Concept

Our business concept is simple, to build a website whereby our clients will be able to upload jobs for energy raters to quote on and subsequent complete the work if their quote is selected. To link energy ratings that are required with energy raters via our website. Similarly to the velk website, jobs will be “advertised” on the job board and raters will select which jobs they wish to quote for.

I have attached a Word document explaining all the parts of the website and another word document showing what we are sort of after and a excel spreadsheet as well. Please read these in conjunction with this brief!
Updates

Dear All

I have submitted with my brief a word doc and excel spreadsheet of the two pages I want created.  However this is not the layout or design I want, I only put it together so that you will need to know what is required on each page.  Feel free to change and redesign it all.

Also the second page does not require the "process" logo or any other menu items except the first five being Home, How it works, About Us, testimonials and Contact us as per the home page.

We also are looking for something very professional and very clean.  It should be very easy to see exactly what you are looking for.

I will also extend the deadline for new designers!!  I am excited to see your talents!!

Thanks

I have increase budget and posted a note saying feel free to change all the details layout etc on my brief just include everything!!! 

Wanting a professional corporate look...

Want a professional corporate look

We have changed our minds and you we no longer require the process to be on the home page.

Thanks

Target Market(s)

Target Market

Home Inspection Companies
Pest Inspection Companies
Residential home buyers/sellers
Real Estate companies

Industry/Entity Type

It Company

Number of Pages Required

1 page

Requirements
Must have
• Colours and Styles

• The website should be mainly white as I believe it is seen as clean and simple with colour from the logos, but can be swayed if it projects the image we are after.

• It should be obvious and process orientated and I do believe symbols, pictures, etc should replace words where possible.

```html
<!DOCTYPE html>
<html lang="en">
<head>
<meta charset="utf-8">
<title>Ratelio Australia – Energy Rating Job Board</title>
<link href="https://fonts.googleapis.com/css2?family=PT+Sans:wght@400;700&family=Arimo:wght@400;700&family=Noto+Serif:ital,wght@1,400;1,700&display=swap" rel="stylesheet">
<style>
:root{
  --bg-top:#6cb53a;
  --bg-bottom:#22934a;
  --nav:#1f7a42;
  --nav-dark:#17663a;
  --orange:#e8a422;
  --orange-dark:#c9740e;
  --leaf:#7cb332;
  --leaf-light:#a9c63a;
  --title-green:#3a9f36;
  --heading-green:#2c9a4a;
  --rust:#b9560e;
  --gold:#e0900e;
  --text:#444;
  --muted:#777;
  --white:#fff;
  --panel:#f5f5f5;
}
*{box-sizing:border-box;margin:0;padding:0}
html,body{width:1200px;height:2334px;overflow:hidden}
body{font-family:"Arimo",Arial,sans-serif;color:var(--text);background:var(--bg-bottom)}
.page{position:relative;width:1200px;height:1166px;background:linear-gradient(180deg,var(--bg-top) 0,var(--bg-bottom) 420px,var(--bg-bottom) 100%)}
.abs{position:absolute}
.sheet{position:absolute;left:74px;top:33px;width:1054px;height:1069px;background:var(--white);border-radius:8px;box-shadow:0 2px 8px rgba(0,0,0,.25)}
.brand{position:absolute;left:69px;top:40px;width:364px;height:137px;background:linear-gradient(180deg,#fff,#f0f0f0);border-radius:6px;box-shadow:0 2px 6px rgba(0,0,0,.25);display:flex;align-items:center;gap:16px;padding-left:30px}
.brand-dot{width:58px;height:58px;border-radius:50%;background:var(--leaf)}
.brand-name{font-family:"PT Sans",sans-serif;font-weight:700;font-size:40px;color:var(--rust);line-height:1}
.main-nav{position:absolute;left:451px;top:31px;width:656px;height:53px;background:linear-gradient(180deg,var(--nav),var(--nav-dark));border-radius:0 0 8px 8px;display:flex;align-items:center;font-family:"PT Sans",sans-serif;font-size:21px}
.main-nav a{color:var(--white);text-decoration:none;padding:0 13px;height:100%;display:flex;align-items:center}
.main-nav a.current{background:rgba(0,0,0,.12)}
.cta{position:absolute;top:104px;width:204px;height:69px;border-radius:6px;background:linear-gradient(180deg,var(--orange),var(--orange-dark));color:var(--white);font-family:"PT Sans",sans-serif;font-size:25px;text-align:center;display:flex;flex-direction:column;justify-content:center;line-height:1.05;box-shadow:0 2px 3px rgba(0,0,0,.2)}
.cta small{font-size:16px;margin-top:3px}
.process{position:absolute;left:96px;top:204px;width:1008px;height:141px;border-radius:10px;background:linear-gradient(180deg,#f0f0f0,#fff 50%,#f0f0f0);display:flex;align-items:center;justify-content:space-around;padding:0 20px;font-family:"PT Sans",sans-serif;font-size:21px;color:#555;text-align:center}
.process .step{width:130px;line-height:1}
.process svg{width:40px;height:60px}
.lead{font-family:"PT Sans",sans-serif;font-weight:700;color:var(--title-green);font-size:20px;line-height:26px}
.body-copy{font-size:16px;line-height:22px;color:#555}
.login{position:absolute;left:791px;top:369px;width:340px;height:199px;background:linear-gradient(180deg,#62a83a,var(--leaf-light));border-radius:6px 0 0 6px;padding:12px 24px;font-family:"PT Sans",sans-serif;color:var(--white)}
.login label{display:flex;align-items:center;gap:8px;font-size:21px}
.login label::before{content:"";width:8px;height:8px;border-radius:50%;background:#2a6a1a;box-shadow:0 0 0 2px #d8f0a0}
.login .field{height:35px;background:var(--white);border-radius:5px;margin:6px 0 14px;font-family:"Arimo",sans-serif;color:#666;font-size:17px;padding:6px 10px;box-shadow:inset 0 1px 3px rgba(0,0,0,.3)}
.login .forgot{font-size:13px;font-family:"Arimo",sans-serif}
.promise{position:absolute;left:70px;top:528px;width:702px;height:157px;border-radius:6px;background:linear-gradient(180deg,#fff,#fde9bf);border:1px solid #f1dfb6;box-shadow:0 1px 3px rgba(0,0,0,.1);padding:18px 34px;font-family:"PT Sans",sans-serif;color:var(--gold)}
.promise p{font-size:24px;line-height:32px}
.promise p+p{font-size:29px;margin-top:14px}
.checklist{list-style:none;font-size:17px;line-height:22px;color:#444}
.checklist li{position:relative;padding-left:40px}
.checklist li::before{content:"";position:absolute;left:0;top:9px;width:8px;height:8px;border-radius:50%;background:var(--leaf)}
.testimonials{position:absolute;left:791px;width:315px;height:427px;border-radius:10px;background:linear-gradient(180deg,#f2f2f2,#fff 20%,#fff 80%,#f2f2f2)}
.testimonials h2{position:absolute;left:14px;top:10px;font-family:"PT Sans",sans-serif;font-weight:400;font-size:31px;color:var(--heading-green)}
.quote{position:absolute;left:10px;width:190px;text-align:right;font-family:"Noto Serif",serif;font-style:italic;font-size:14px;line-height:20px;color:#888}
.quote-mark{position:absolute;font-family:"Noto Serif",serif;font-weight:700;font-size:46px;color:var(--leaf-light);line-height:1}
.portrait{position:absolute;left:209px;width:88px;height:88px;border:2px solid var(--orange);background:linear-gradient(160deg,#c9a07c,#6a4a38)}
.author{position:absolute;left:18px;font-family:"Noto Serif",serif;font-style:italic;font-size:14px;color:#333}
.author b{display:block;font-size:15px}
.author span{font-size:12px;color:#555}
.copyright{position:absolute;left:74px;font-size:13px;color:#a9e08a}
.welcome{position:absolute;left:96px;top:200px;width:675px;height:60px;border-radius:8px 8px 0 0;background:linear-gradient(180deg,#f0f0f0,#fff);display:flex;align-items:center;padding-left:14px;font-family:"PT Sans",sans-serif}
.welcome .bullet{width:14px;height:14px;border-radius:50%;background:var(--leaf);margin-right:12px}
.welcome h1{font-weight:400;font-size:35px;color:var(--rust)}
.welcome h1 span{font-size:27px;color:var(--gold)}
.welcome .edit{margin-left:auto;margin-right:32px;font-family:"Arimo",sans-serif;font-size:13px;color:#2a8f8a;display:flex;align-items:center;gap:8px}
.avatar{position:absolute;left:114px;top:260px;width:163px;height:164px;border:2px solid var(--orange);background:linear-gradient(160deg,#cbb7a8,#3a1a1e 70%,#9a1a2a)}
.profile dt{font-family:"PT Sans",sans-serif;font-size:18px;color:var(--leaf-light);margin-top:8px}
.profile dd{font-family:"Noto Serif",serif;font-size:15px;color:#888}
.tabs{position:absolute;left:114px;top:448px;display:flex;gap:10px}
.tab{height:42px;padding:0 10px;border-radius:6px 6px 0 0;background:linear-gradient(180deg,#3aa84a,#2a8f3e);color:var(--white);font-family:"PT Sans",sans-serif;font-size:21px;display:flex;align-items:center}
.tab.active{background:linear-gradient(180deg,#1f7a42,#2a8f3e)}
.jobs{position:absolute;left:107px;top:490px;width:650px;height:577px;background:linear-gradient(180deg,#8ab436,var(--leaf-light));border-radius:0 6px 6px 6px}
.job{position:absolute;left:15px;width:618px;background:var(--white);border-radius:5px;border:1px solid #d9d9d9;font-size:13px;line-height:17.5px;color:#444}
.job time{position:absolute;left:10px;top:14px;font-size:12px;color:#555}
.job p{position:absolute;left:136px;top:13px;width:350px}
.job .actions{position:absolute;left:522px;top:8px;display:flex;gap:9px;align-items:center}
.tip{position:absolute;left:707px;top:533px;background:#ffff9a;border:1px solid #c9c96a;font-size:11px;padding:3px 5px;color:#444}
.pager{position:absolute;left:465px;top:552px;font-family:"PT Sans",sans-serif;font-size:16px;color:#2a5a1a;display:flex;gap:6px;align-items:center}
.pager b{color:#fff}
.pager .tri{width:0;height:0;border-top:5px solid transparent;border-bottom:5px solid transparent}
</style>
</head>
<body>

<svg width="0" height="0" style="position:absolute">
  <defs>
    <symbol id="chevron" viewBox="0 0 40 60"><path d="M8 6 L32 30 L8 54" fill="none" stroke="#2f9a46" stroke-width="11" stroke-linejoin="round" stroke-linecap="round"/></symbol>
    <symbol id="tick" viewBox="0 0 20 18"><path d="M2 9 L8 15 L18 2" fill="none" stroke="#5aa82a" stroke-width="4" stroke-linecap="round"/></symbol>
    <symbol id="cross" viewBox="0 0 18 18"><path d="M3 3 L15 15 M15 3 L3 15" stroke="#c8181c" stroke-width="4.5" stroke-linecap="round"/></symbol>
    <symbol id="mail" viewBox="0 0 32 22"><rect x="1" y="1" width="30" height="20" rx="2" fill="#f4f4f4" stroke="#bbb"/><path d="M1 2 L16 13 L31 2" fill="none" stroke="#bbb"/></symbol>
  </defs>
</svg>

<!-- Home page -->
<section class="page">
  <div class="sheet"></div>
  <div class="brand"><span class="brand-dot"></span><span class="brand-name">Ratelio<br>Australia</span></div>
  <nav class="main-nav"><a class="current">HOME</a><a>HOW IT WORKS?</a><a>ABOUT US</a><a>TESTIMONIALS</a><a>CONTACT US</a></nav>
  <a class="cta" style="left:459px">GET A QUOTE</a>
  <a class="cta" style="left:677px">ENERGY RATERS<small>Add your business</small></a>
  <a class="cta" style="left:894px">ACTIVE<br>JOB BOARD</a>

  <div class="process">
    <div class="step">Post a job</div><svg><use href="#chevron"/></svg>
    <div class="step">Get as many quotes as you like</div><svg><use href="#chevron"/></svg>
    <div class="step">Select energy quote that suits</div><svg><use href="#chevron"/></svg>
    <div class="step">Approve payment</div><svg><use href="#chevron"/></svg>
    <div class="step">Receive Rating</div>
  </div>

  <p class="lead abs" style="left:104px;top:366px;width:660px">We provide you with solutions to your energy rating needs!&nbsp; Get up to 10 competitive quotes for your energy ratings from our database of professional accredited energy raters in all states and territories!</p>
  <p class="body-copy abs" style="left:104px;top:462px;width:640px">Ratelio australia is Australia's leading professional energy rating consultancy firm specializing in large scaled residential and commercial energy rating logistics.</p>

  <form class="login">
    <label>User</label><div class="field">lumoreno</div>
    <label>Password</label><div class="field">&#9679;&#9679;&#9679;&#9679;&#9679;&#9679;&#9679;&#9679;&#9679;&#9679;</div>
    <div class="forgot">Did you forget your password</div>
  </form>

  <div class="promise">
    <p>It's Free, Fast and Easy to use and you get the best price and turnaround time that suits you!!</p>
    <p>Its a one stop shop for your energy rating needs!!</p>
  </div>

  <p class="abs" style="left:104px;top:702px;width:660px;font-family:'PT Sans',sans-serif;font-weight:700;font-size:18px;line-height:22px;color:#888">Register with us, upload your job and specifications, and sit back and watch as energy raters provide quotes for your work!</p>
  <ul class="checklist abs" style="left:104px;top:768px">
    <li>Get up to 10 best priced quotes for your energy ratings</li>
    <li>You save time</li>
    <li>Be able to specify your desired turnaround times</li>
    <li>You can upload a job for quoting anytime and anywhere</li>
    <li>Choose a deadline for energy raters to supply quotes</li>
    <li>Be able to track your numerous jobs in one place</li>
  </ul>
  <p class="abs" style="left:104px;top:940px;width:650px;font-weight:700;font-size:17px;line-height:22px;color:#333">Its totally free to be registered with us and there is no obligations or hidden catches!</p>

  <aside class="testimonials" style="top:607px">
    <h2>TESTIMONIALS</h2>
    <span class="quote-mark" style="left:10px;top:52px">&ldquo;</span>
    <p class="quote" style="top:54px">Lorem ipsum dolor sit amet, consectetur adipiscing elit. Phasellus arcu magna, condimentum id consequat quis,</p>
    <div class="portrait" role="img" aria-label="Portrait photo of client Helena Varga" style="top:59px"></div>
    <p class="author" style="top:186px"><b>Helena Varga</b><span>Porto, Portugal</span></p>
    <span class="quote-mark" style="left:268px;top:196px">&rdquo;</span>
    <span class="quote-mark" style="left:10px;top:254px">&ldquo;</span>
    <p class="quote" style="top:256px">Lorem ipsum dolor sit amet, consectetur adipiscing elit. Phasellus arcu</p>
    <div class="portrait" role="img" aria-label="Portrait photo of client Owen Mitchell" style="top:261px;background:linear-gradient(160deg,#d9d9d9,#444)"></div>
    <p class="author" style="top:367px"><b>Owen Mitchell</b><span>Oregon, United States</span></p>
    <span class="quote-mark" style="left:268px;top:376px">&rdquo;</span>
  </aside>

  <p class="copyright" style="top:1114px">Copyright 2010 - Ratelio Australia - All rights reserved</p>
</section>

<!-- Client job board -->
<section class="page">
  <div class="sheet"></div>
  <div class="brand"><span class="brand-dot"></span><span class="brand-name">Ratelio<br>Australia</span></div>
  <nav class="main-nav"><a class="current">HOME</a><a>HOW IT WORKS?</a><a>ABOUT US</a><a>TESTIMONIALS</a><a>CONTACT US</a></nav>
  <a class="cta" style="left:459px">GET A QUOTE</a>
  <a class="cta" style="left:677px">ENERGY RATERS<small>Add your business</small></a>
  <a class="cta" style="left:894px">ACTIVE<br>JOB BOARD</a>

  <header class="welcome">
    <span class="bullet"></span>
    <h1>Welcome, <span>Lucia Moreno</span></h1>
    <span class="edit"><svg width="18" height="18" viewBox="0 0 18 18"><path d="M3 15 L4 11 L13 2 L16 5 L7 14 Z" fill="#f0b030" stroke="#b07010"/></svg>Edit profile</span>
  </header>
  <div class="avatar" role="img" aria-label="Profile photo of Lucia Moreno"></div>
  <dl class="profile abs" style="left:293px;top:262px">
    <dt>Name</dt><dd>Lucia Isabel Moreno Tan</dd>
    <dt>E-mail</dt><dd>lumoreno@mailbox.test</dd>
    <dt>Profession</dt><dd>Digital designer</dd>
  </dl>

  <div class="tabs"><span class="tab active">QUOTING JOBS</span><span class="tab">ACTIVE JOBS</span><span class="tab">COMPLEATE JOBS</span></div>
  <div class="jobs">
    <article class="job" style="top:16px;height:126px"><time>Mon, 29 March 2010</time><p>Lorem ipsum dolor sit amet, consectetur adipiscing elit. Vestibulum sed fermentum lectus. Suspendisse aliquam, justo eu luctus placerat, orci purus eleifend est, ut ornare metus elit quis ligula. Morbi vitae sapien velit. Aliquam erat volutpat. Cras luctus imperdiet ante, sit amet blandit diam porttitor at.</p><div class="actions"><svg width="20" height="18"><use href="#tick"/></svg><svg width="18" height="18"><use href="#cross"/></svg><svg width="32" height="22"><use href="#mail"/></svg></div></article>
    <article class="job" style="top:159px;height:76px"><time>Mon, 29 March 2010</time><p>Lorem ipsum dolor sit amet, consectetur adipiscing elit. Vestibulum sed fermentum lectus. Suspendisse aliquam, justo eu luctus placerat, orci purus eleifend est, ut ornare</p><div class="actions"><svg width="20" height="18"><use href="#tick"/></svg><svg width="18" height="18"><use href="#cross"/></svg><svg width="32" height="22"><use href="#mail"/></svg></div></article>
    <article class="job" style="top:252px;height:56px"><time>Mon, 29 March 2010</time><p>Lorem ipsum dolor sit amet, consectetur adipiscing elit. Vestibulum sed fermentum lectus. Suspendisse</p><div class="actions"><svg width="20" height="18"><use href="#tick"/></svg><svg width="18" height="18"><use href="#cross"/></svg><svg width="32" height="22"><use href="#mail"/></svg></div></article>
    <article class="job" style="top:327px;height:126px"><time>Mon, 29 March 2010</time><p>Lorem ipsum dolor sit amet, consectetur adipiscing elit. Vestibulum sed fermentum lectus. Suspendisse aliquam, justo eu luctus placerat, orci purus eleifend est, ut ornare metus elit quis ligula. Morbi vitae sapien velit. Aliquam erat volutpat. Cras luctus imperdiet ante, sit amet blandit diam porttitor at.</p><div class="actions"><svg width="20" height="18"><use href="#tick"/></svg><svg width="18" height="18"><use href="#cross"/></svg><svg width="32" height="22"><use href="#mail"/></svg></div></article>
    <article class="job" style="top:471px;height:57px"><time>Mon, 29 March 2010</time><p>Lorem ipsum dolor sit amet, consectetur adipiscing elit. Vestibulum sed fermentum lectus. Suspendisse</p><div class="actions"><svg width="20" height="18"><use href="#tick"/></svg><svg width="18" height="18"><use href="#cross"/></svg><svg width="32" height="22"><use href="#mail"/></svg></div></article>
    <div class="pager">previous <span class="tri" style="border-right:6px solid #d8ec9a"></span><b>1</b> 2 3 <span class="tri" style="border-left:6px solid #d8ec9a"></span> next</div>
  </div>
  <span class="tip">Email the energy rater</span>

  <aside class="testimonials" style="top:200px">
    <h2>TESTIMONIALS</h2>
    <span class="quote-mark" style="left:10px;top:52px">&ldquo;</span>
    <p class="quote" style="top:54px">Lorem ipsum dolor sit amet, consectetur adipiscing elit. Phasellus arcu magna, condimentum id consequat quis,</p>
    <div class="portrait" role="img" aria-label="Portrait photo of client Helena Varga" style="top:59px"></div>
    <p class="author" style="top:186px"><b>Helena Varga</b><span>Porto, Portugal</span></p>
    <span class="quote-mark" style="left:268px;top:196px">&rdquo;</span>
    <span class="quote-mark" style="left:10px;top:254px">&ldquo;</span>
    <p class="quote" style="top:256px">Lorem ipsum dolor sit amet, consectetur adipiscing elit. Phasellus arcu</p>
    <div class="portrait" role="img" aria-label="Portrait photo of client Owen Mitchell" style="top:261px;background:linear-gradient(160deg,#d9d9d9,#444)"></div>
    <p class="author" style="top:367px"><b>Owen Mitchell</b><span>Oregon, United States</span></p>
    <span class="quote-mark" style="left:268px;top:376px">&rdquo;</span>
  </aside>

  <p class="lead abs" style="left:791px;top:658px;width:320px">We provide you with solutions to your energy rating needs!&nbsp; Get up to 10 competitive quotes for your energy ratings from our database of professional accredited energy raters in all states and territories!</p>
  <p class="body-copy abs" style="left:791px;top:831px;width:320px;font-size:17px">Ratelio australia is Australia's leading professional energy rating consultancy firm specializing in large scaled residential and commercial energy rating logistics.</p>

  <p class="copyright" style="top:1114px">Copyright 2010 - Ratelio Australia - All rights reserved</p>
</section>

</body>
</html>
```